professional business card design

Business card design. Photos have been uploaded and i am open to the designer choosing which photos to use. Would like the card to be mostyly in a grey scale design with black, whites, silver & grey colours. I have added copy of our flyer as would like on the back side of card our services to be listed. Do not use any bright colurs such as blue red green or yellow. i need to be able to edit the phone number and naem in the final card design submitted.

Target Market(s)

Clients

Industry/Entity Type

earhmovibng and transport

Contact Information for Business Card

Director Name, address, email, phone number and services

Colors

Designer to choose only greyscale colors for use in the design.

Requirements
Should not have
• no yellow, red, blue or green

```html
<!DOCTYPE html>
<html lang="en">
<head>
<meta charset="utf-8">
<title>KRT PTY LTD – Business Card</title>
<link rel="stylesheet" href="https://fonts.googleapis.com/css2?family=Arimo:ital,wght@0,400;0,700;1,400&family=Michroma&display=swap">
<style>
  :root {
    --page: #d7d7d7;
    --card-black: #0b0b0b;
    --panel-dark: #1c1c1c;
    --silver-light: #f2f2f2;
    --silver-mid: #bdbdbd;
    --silver-dark: #7a7a7a;
    --text-light: #f4f4f4;
    --text-muted: #a9a9a9;
    --text-dark: #111111;
  }
  * { box-sizing: border-box; margin: 0; padding: 0; }
  html, body { width: 1075px; height: 1200px; overflow: hidden; }
  body {
    background: var(--page);
    font-family: "Arimo", Arial, sans-serif;
    position: relative;
  }
  .card {
    position: absolute;
    left: 206px;
    width: 663px;
    height: 395px;
    background: var(--card-black);
    overflow: hidden;
    box-shadow: 0 2px 6px rgba(0,0,0,0.35);
  }
  .card--front { top: 187px; }
  .card--back { top: 637px; }

  .silver {
    background: linear-gradient(90deg, var(--silver-dark) 0%, var(--silver-light) 35%, var(--silver-mid) 65%, var(--silver-light) 85%, var(--silver-dark) 100%);
  }

  /* Front */
  .front-backdrop {
    position: absolute; left: 0; top: 0; width: 663px; height: 243px;
    background: radial-gradient(ellipse at 55% 30%, #3a3a3a 0%, #1a1a1a 55%, #0d0d0d 100%);
  }
  .brand-name {
    position: absolute; top: 46px; left: 0; width: 663px; text-align: center;
    font-family: "Michroma", sans-serif; font-size: 64px; letter-spacing: 4px;
    color: var(--silver-mid); line-height: 1;
  }
  .fleet-photo {
    position: absolute; left: 36px; top: 118px; width: 627px; height: 125px;
    background: linear-gradient(180deg, #4a4a4a 0%, #2a2a2a 60%, #151515 100%);
  }
  .company-bar { position: absolute; top: 243px; height: 38px; }
  .company-bar--name { left: 0; width: 331px; }
  .company-bar--icon { left: 336px; width: 58px; }
  .company-bar--phone { left: 399px; width: 264px; }
  .company-bar span {
    display: block; font-family: "Michroma", sans-serif; font-size: 21px;
    line-height: 38px; color: var(--text-dark); font-weight: 700;
    -webkit-text-stroke: 0.6px var(--text-dark);
  }
  .company-bar--name span { padding-left: 36px; letter-spacing: 2px; }
  .company-bar--phone span { text-align: center; letter-spacing: 2px; }
  .company-bar--icon svg { display: block; margin: 8px auto 0; }

  .person { position: absolute; left: 35px; top: 294px; color: var(--text-light); }
  .person-name { font-size: 24px; font-weight: 700; letter-spacing: 1.5px; }
  .person-role { font-size: 17px; margin-top: 3px; color: #dcdcdc; }

  .contact { position: absolute; right: 42px; top: 296px; text-align: right; color: var(--text-light); font-size: 17px; line-height: 24px; }
  .contact li { list-style: none; display: flex; justify-content: flex-end; align-items: center; gap: 10px; }
  .contact svg { flex: none; }

  .address-bar {
    position: absolute; left: 0; top: 357px; width: 663px; height: 38px;
    text-align: center; font-size: 18px; line-height: 38px; color: var(--text-dark);
  }
  .address-bar strong { font-weight: 700; }

  /* Back */
  .back-backdrop {
    position: absolute; left: 0; top: 0; width: 342px; height: 395px;
    background: linear-gradient(180deg, #1a1a1a 0%, #262626 55%, #141414 100%);
  }
  .truck-photo {
    position: absolute; left: 0; top: 85px; width: 320px; height: 260px;
    background: radial-gradient(ellipse at 50% 50%, #d9d9d9 0%, #9a9a9a 45%, #3a3a3a 85%, rgba(30,30,30,0) 100%);
  }
  .services-tab {
    position: absolute; left: 226px; top: 0; width: 210px; height: 42px;
    text-align: center; line-height: 44px; font-weight: 700; font-size: 19px;
    letter-spacing: 0.5px; color: var(--text-dark);
  }
  .services-list { position: absolute; left: 364px; top: 50px; list-style: none; color: #e6e6e6; font-size: 17px; line-height: 20.6px; }
  .services-list li { position: relative; padding-left: 16px; }
  .services-list li::before {
    content: ""; position: absolute; left: 0; top: 6px; width: 9px; height: 9px;
    border-radius: 50%; background: var(--text-light);
  }
  .services-list .wrap { display: block; }
  .tagline { position: absolute; left: 363px; top: 310px; width: 290px; font-style: italic; font-size: 17px; line-height: 20.6px; color: var(--text-muted); }
  .tagline em { color: var(--text-light); }
</style>
</head>
<body>

<section class="card card--front" aria-label="Business card front">
  <div class="front-backdrop"></div>
  <div class="brand-name">KRT</div>
  <div class="fleet-photo" role="img" aria-label="Photo of a road train prime mover towing three tipper trailers"></div>

  <div class="company-bar company-bar--name silver"><span>KRT PTY LTD</span></div>
  <div class="company-bar company-bar--icon silver">
    <svg width="22" height="22" viewBox="0 0 24 24" aria-label="Phone">
      <path d="M6.6 10.8a15 15 0 0 0 6.6 6.6l2.2-2.2c.3-.3.7-.4 1-.2 1.1.4 2.3.6 3.6.6.6 0 1 .4 1 1V20c0 .6-.4 1-1 1A17 17 0 0 1 3 4c0-.6.4-1 1-1h3.5c.6 0 1 .4 1 1 0 1.3.2 2.5.6 3.6.1.3 0 .7-.2 1z" fill="#111"/>
      <path d="M15 3a6 6 0 0 1 6 6M15 6.5A2.5 2.5 0 0 1 17.5 9" stroke="#111" stroke-width="1.6" fill="none"/>
    </svg>
  </div>
  <div class="company-bar company-bar--phone silver"><span>000 123 456</span></div>

  <div class="person">
    <div class="person-name">DANIEL HARTLEY</div>
    <div class="person-role">Managing Director</div>
  </div>

  <ul class="contact">
    <li>email@websitename.com
      <svg width="18" height="13" viewBox="0 0 18 13"><rect x="0.5" y="0.5" width="17" height="12" fill="#f4f4f4"/><path d="M0.5 0.5 9 7.5 17.5 0.5M0.5 12.5 6.5 6M17.5 12.5 11.5 6" stroke="#0b0b0b" stroke-width="1.2" fill="none"/></svg>
    </li>
    <li>www.website.com
      <svg width="17" height="17" viewBox="0 0 20 20"><g fill="none" stroke="#f4f4f4" stroke-width="1.6"><circle cx="10" cy="10" r="8.5"/><ellipse cx="10" cy="10" rx="3.8" ry="8.5"/><path d="M1.5 10h17M3 5.5h14M3 14.5h14"/></g></svg>
    </li>
  </ul>

  <div class="address-bar silver"><strong>Address:</strong> Address Line Goes Here, Adress line and pincode here</div>
</section>

<section class="card card--back" aria-label="Business card back">
  <div class="back-backdrop"></div>
  <div class="truck-photo" role="img" aria-label="Photo of a white prime mover truck with an oversize sign on the bumper"></div>
  <div class="services-tab silver">OUR SERVICES</div>

  <ul class="services-list">
    <li>Over size loads/hot shot loads</li>
    <li>Heavy vehicle recovery services</li>
    <li>Potable water deliveries</li>
    <li>Road building/mainttenance</li>
    <li>Earthworks</li>
    <li>Sand &amp; metal supply &amp;&nbsp; cartage</li>
    <li>Road train tippers</li>
    <li>Road train tankers</li>
    <li>Road train flat tops</li>
    <li>Drop deck trailers</li>
    <li>Mine site accredited<span class="wrap">Equipment &amp; operators</span></li>
  </ul>

  <p class="tagline">We offer a large range of services not listed so <em>Call us today for a personalised quote to suit your needs.</em></p>
</section>

</body>
</html>
```